Verlindo Magician

I want the business card for my business to give to people who watch that later I will be employed to show magic here is my website http://www.balsamomagicien.com/I want the interesting design , i am very opened for formal and informal, I watch a lot of design so don't stick to the common shape and form but i hope it can also be produced the thing to write on will be the same as in picture that i will upload , i also will upload the logo for you that so can be easy to useDenis CostilleMagicianMAGICIAN BALSAMO 17 rue des Tilleuls - 25000 BESANÇON contact@verlindoillusions.example tel. 0381 946 157 tel. 0674 219 503

```html
<!DOCTYPE html>
<html lang="en">
<head>
<meta charset="utf-8">
<title>Verlindo Magician – Business Card</title>
<link rel="stylesheet" href="https://fonts.googleapis.com/css2?family=Jost:wght@400;600&family=Open+Sans:wght@400;700&display=swap">
<style>
  :root {
    --backdrop: #8a5a34;
    --kraft-light: #dcb584;
    --kraft-dark: #b98a59;
    --ink: #1c140b;
    --rule: #8f7050;
    --figure-tone: #2a1d12;
  }
  * { margin: 0; padding: 0; box-sizing: border-box; }
  html, body {
    width: 1200px;
    height: 900px;
    overflow: hidden;
    background: var(--backdrop);
  }
  .stage {
    position: relative;
    width: 1200px;
    height: 900px;
  }
  .card {
    position: absolute;
    left: 330px;
    width: 557px;
    height: 343px;
    background: linear-gradient(135deg, var(--kraft-light) 0%, var(--kraft-dark) 100%);
    color: var(--ink);
    text-align: center;
    font-family: "Open Sans", Arial, sans-serif;
  }
  .card--front { top: 90px; }
  .card--back { top: 470px; }

  .holder-name {
    position: absolute;
    top: 64px;
    left: 0;
    right: 0;
    font-family: "Jost", "Century Gothic", sans-serif;
    font-weight: 600;
    font-size: 23px;
    line-height: 28px;
    letter-spacing: 0.2px;
  }
  .holder-role {
    position: absolute;
    top: 89px;
    left: 0;
    right: 0;
    font-size: 16px;
    line-height: 20px;
  }
  .divider {
    position: absolute;
    left: 217px;
    width: 136px;
    height: 1px;
    background: var(--rule);
  }
  .divider--upper { top: 117px; }
  .divider--lower { top: 223px; }

  .contact-list {
    position: absolute;
    top: 130px;
    left: 0;
    right: 0;
    list-style: none;
    font-size: 16px;
    line-height: 20.5px;
  }
  .contact-list b { font-weight: 700; }

  .business {
    position: absolute;
    top: 234px;
    left: 0;
    right: 0;
    font-size: 16px;
    line-height: 20.5px;
  }
  .business-name { font-weight: 700; }

  .figure-area {
    position: absolute;
    left: 210px;
    top: 66px;
    width: 138px;
    height: 170px;
    border-radius: 40px 40px 14px 14px;
    background: linear-gradient(180deg, var(--figure-tone) 0%, #3a2817 100%);
  }
  .brand-name {
    position: absolute;
    top: 236px;
    left: 0;
    right: 0;
    font-family: "Jost", "Century Gothic", sans-serif;
    font-weight: 400;
    font-size: 28px;
    line-height: 34px;
    letter-spacing: 1px;
  }
</style>
</head>
<body>
  <main class="stage">
    <section class="card card--front">
      <h1 class="holder-name">MARC RAVOULET</h1>
      <p class="holder-role">Magician</p>
      <div class="divider divider--upper"></div>
      <ul class="contact-list">
        <li><b>P:</b> 0381 946 157</li>
        <li><b>P:</b> 0674 219 503</li>
        <li><b>E:</b> contact@verlindoillusions.example</li>
        <li><b>W:</b> www.verlindoillusions.example</li>
      </ul>
      <div class="divider divider--lower"></div>
      <div class="business">
        <p class="business-name">MAGICIAN VERLINDO</p>
        <p class="business-address">17 rue des Tilleuls - 25000 BESANÇON</p>
      </div>
    </section>

    <section class="card card--back">
      <div class="figure-area" role="img" aria-label="Illustration of the magician in a dark jacket holding up a playing card"></div>
      <p class="brand-name">VERLINDO</p>
    </section>
  </main>
</body>
</html>
```